Wordpress Web Design & Coding for velcorahealth.ca

We need a website for a new investment company that is visually grabbing and vibrant. We would like to see a web page that displays trust, growth and confidence. Needs to be responsive and mobile friendly for all browsers and coded for both Android & IOS.

Open to the number of pages and menu items. I selected 4 but if you feel the layout would work better with less I am open to this. Need to sell the people (management team/related businesses) and then show where the invested money will be going (upcoming projects).

Company Info:

Vel Cora is an investment company put together by a group of seasoned business professionals who have come together to combine decades of success in the real estate development, management, financing and medical services. The company will be a full service company offering turn key solutions for medical professionals.

Vel-Cora will focus on providing a full range of services via a group of distinct companies to deliver newly emerging needs of the medical community. The end goal will be to create complete solutions for individuals in the medical community. Our group has experience and success with the conceptualization, construction and financing of medical and dental clinic spaces. Vel-Cora Solutions will be established to accommodate all areas of the development and creation of clinics for medical professionals from building construction to equipment financing and administrations.

You can mention these companies and take photos from their websites. You can also use stock photos.

Our construction partner:
https://318bld.com/projects/

Our equipment leasing partner:
https://www.norvixa.com/

Our Management Team and medical partners

Gil Parish
https://www.ourfirmstance.ca/

Dietmar Vellasquin
https://www.gshdentalservices.com/about-us

PROPOSED PROJECTS (see attachment for details)
Pinegrove Business Park
Holtmere Business Park
Mt. Corwin Ridge Professional

Target Market(s)

Investors

Industry/Entity Type

Investment

Coding

Coded - Design and coding required

Number of Pages Required

4 page

Font styles to use
Sans Serif

Requirements
Must have
• Wordpress – must be both desktop and mobile friendly with fast page load speed
Ability to edit after ourselves in Wordpress
Attractive home page with logo etc.
Logo colours are: for the blue the pantone color is #0355a3
and for the green is #8cc63f

Sections, about us, what we do/services we provide, contact us

```html
<!DOCTYPE html>
<html lang="en">
<head>
<meta charset="utf-8">
<title>Vel-Cora Solutions</title>
<link rel="stylesheet" href="https://fonts.googleapis.com/css2?family=Poppins:wght@300;400;500;600;700&display=swap">
<style>
:root{
  --blue:#0355a3;
  --green:#8cc63f;
  --ink:#1b1b1b;
  --text:#555;
  --dark:#2f3338;
  --footer:#353535;
  --light:#f7f7f7;
  --ghost:#eeeeee;
}
*{margin:0;padding:0;box-sizing:border-box}
html,body{width:1200px;height:4227px;overflow:hidden}
body{position:relative;font-family:'Poppins',sans-serif;color:var(--ink);background:#fff}
.abs{position:absolute}
.photo{position:absolute}

/* header */
.site-header{position:absolute;left:0;top:0;width:1200px;height:148px;background:#fff}
.brand{position:absolute;left:110px;top:30px;display:flex;align-items:center;gap:12px}
.brand-mark{width:34px;height:34px;background:var(--blue)}
.brand-name{font-weight:600;color:var(--blue);font-size:30px;line-height:1;letter-spacing:1px}
.brand-name small{display:block;font-size:19px;letter-spacing:3px;margin-top:6px}
.contact-phone{position:absolute;left:752px;top:22px;display:flex;align-items:center;gap:8px;color:var(--blue);font-size:17px;font-weight:500}
.icon-ring{width:42px;height:42px;border:2px solid var(--blue);border-radius:50%;display:flex;align-items:center;justify-content:center}
.social{position:absolute;display:flex;gap:6px}
.social span{width:42px;height:42px;border:2px solid #333;border-radius:50%;display:block}
.main-nav{position:absolute;right:111px;top:96px;display:flex;gap:29px;font-size:14px;font-weight:500;text-transform:uppercase}
.main-nav .active{color:var(--green)}

/* hero */
.hero{position:absolute;left:0;top:148px;width:1200px;height:515px;background:linear-gradient(180deg,#4a5866 0%,#6a7480 45%,#3e4247 100%)}
.hero-shade{position:absolute;inset:0;background:linear-gradient(90deg,rgba(0,0,0,.55),rgba(0,0,0,.15))}
.hero h1{position:absolute;left:110px;top:115px;font-size:52px;font-weight:700;color:#fff;letter-spacing:.5px}
.hero p{position:absolute;left:110px;top:190px;width:560px;font-size:17px;line-height:27px;color:#fff}
.btn-outline-light{position:absolute;left:110px;top:272px;width:113px;height:57px;border:3px solid #fff;color:#fff;font-size:14px;font-weight:500;display:flex;align-items:center;justify-content:center}

/* section headings */
.ghost{position:absolute;font-size:80px;font-weight:700;color:var(--ghost);white-space:nowrap;line-height:1}
.section-title{position:absolute;font-size:32px;font-weight:600;color:var(--ink);white-space:nowrap;line-height:1}
.center{left:0;width:1200px;text-align:center}

/* about */
.about-frame{position:absolute;left:110px;top:791px;width:348px;height:414px;border:2px solid #333}
.about-photo{left:128px;top:773px;width:348px;height:416px;border:2px solid #333;background:linear-gradient(180deg,#5b7bc4 0%,#9aa0a6 35%,#4a4a4a 75%,#4f7a2c 100%)}
.about-copy{position:absolute;left:515px;top:830px;width:575px}
.about-copy h3{font-size:20px;font-weight:400;margin-top:46px}
.about-copy p{font-size:13px;line-height:22px;color:var(--text);margin-top:14px}
.btn-outline-dark{position:absolute;left:515px;top:1098px;width:127px;height:55px;border:2px solid #222;font-size:17px;display:flex;align-items:center;justify-content:center}

/* services */
.services-band{position:absolute;left:0;top:1290px;width:1200px;height:500px;background:linear-gradient(180deg,#3a3f46,#2c3036)}
.services-band .lead-small{position:absolute;top:68px;font-size:18px;font-weight:500;color:#fff}
.services-band h2{position:absolute;top:95px;font-size:31px;font-weight:500;color:#fff}
.services-band p{position:absolute;left:130px;width:940px;top:147px;font-size:14px;line-height:26px;color:#fff;text-align:center}
.service-card{position:absolute;top:1556px;width:302px;height:512px;background:#fff;box-shadow:0 2px 8px rgba(0,0,0,.15)}
.service-card .photo{left:0;top:0;width:302px;height:234px}
.service-card h3{position:absolute;left:16px;top:260px;font-size:21px;font-weight:400}
.service-card p{position:absolute;left:16px;top:298px;width:270px;font-size:13px;line-height:23px;color:var(--text);text-align:justify}
.btn-small{position:absolute;left:16px;top:428px;width:98px;height:47px;font-size:14px;display:flex;align-items:center;justify-content:center}
.blue-text{color:var(--blue)}
.green-text{color:var(--green)}
.btn-blue-outline{border:2px solid var(--blue);color:var(--blue)}
.btn-green{background:var(--green);color:#fff}
.btn-blue{background:var(--blue);color:#fff}

/* partners */
.partner-box{position:absolute;top:2290px;width:333px;height:155px;background:#fff;box-shadow:0 1px 6px rgba(0,0,0,.12);display:flex;flex-direction:column;align-items:center;justify-content:center;gap:6px}
.partner-box .name{font-size:24px;font-weight:500;letter-spacing:2px}
.partner-box .sub{font-size:12px;color:var(--text)}

/* team */
.team-band{position:absolute;left:0;top:2530px;width:1200px;height:593px;background:var(--light)}
.team-card{position:absolute;top:2710px;width:470px;height:337px;background:#fff;box-shadow:0 1px 6px rgba(0,0,0,.1)}
.team-card .photo{left:0;top:0;width:220px;height:337px}
.team-card h3{position:absolute;left:234px;top:30px;font-size:21px;font-weight:500}
.team-card p{position:absolute;left:234px;top:70px;width:222px;font-size:13px;line-height:22.5px;color:var(--text);text-align:justify}
.team-card .btn-small{left:234px;top:258px;width:100px;height:46px}

/* projects */
.project-card{position:absolute;top:3310px;width:313px;height:378px;border:2px solid #ddd;background:#fff}
.project-card .photo{left:0;top:0;width:309px;height:296px}
.project-card .label{position:absolute;left:0;top:296px;width:309px;height:78px;display:flex;align-items:center;justify-content:center;font-size:17px;font-weight:500;text-transform:uppercase;text-align:center}
.project-card.featured .label{background:var(--green);color:#fff}

/* footer */
.site-footer{position:absolute;left:0;top:3785px;width:1200px;height:442px;background:var(--footer);color:#fff}
.footer-brand{position:absolute;left:110px;top:150px;font-weight:600;font-size:56px;line-height:1;letter-spacing:1px}
.footer-brand small{display:block;font-size:31px;letter-spacing:5px;margin-top:10px}
.quick-links h4{position:absolute;left:484px;top:80px;font-size:25px;font-weight:400}
.quick-links ul{position:absolute;list-style:none;font-size:16px;line-height:30px}
.footer-contact{position:absolute;left:817px;top:70px}
.contact-row{display:flex;gap:12px;margin-bottom:28px}
.contact-icon{width:52px;height:52px;border-radius:50%;background:var(--green);display:flex;align-items:center;justify-content:center;flex:none}
.contact-row b{display:block;font-size:16px;font-weight:500}
.contact-row span{font-size:14px;line-height:24px}
.footer-rule{position:absolute;left:110px;top:343px;width:980px;height:1px;background:#555}
.copyright{position:absolute;left:110px;top:374px;font-size:16px}
.footer-social{position:absolute;left:941px;top:365px;display:flex;gap:8px}
.footer-social span{width:42px;height:42px;border:2px solid #fff;border-radius:50%;display:block}
</style>
</head>
<body>

<header class="site-header">
  <div class="brand"><span class="brand-mark"></span><div class="brand-name">VEL-CORA<small>SOLUTIONS</small></div></div>
  <div class="contact-phone">
    <span class="icon-ring"><svg width="20" height="20" viewBox="0 0 24 24" fill="none" stroke="#0355a3" stroke-width="2"><path d="M5 3h4l2 5-3 2a11 11 0 0 0 6 6l2-3 5 2v4a2 2 0 0 1-2 2A17 17 0 0 1 3 5a2 2 0 0 1 2-2z"/></svg></span>
    +1 555 014 2290
  </div>
  <div class="social" style="left:947px;top:22px"><span></span><span></span><span></span></div>
  <nav class="main-nav"><span class="active">Home</span><span>About Us</span><span>Our Services</span><span>What We Do</span><span>Contact Us</span></nav>
</header>

<section class="hero">
  <div class="photo" role="img" aria-label="Modern commercial building exterior under an evening sky" style="inset:0;background:linear-gradient(180deg,#52606e,#8a9098 55%,#3a3d41)"></div>
  <div class="hero-shade"></div>
  <h1>VEL-CORA SOLUTIONS</h1>
  <p>Vel Cora is an investment company put together by a group of seasoned business professionals.</p>
  <div class="btn-outline-light">READ MORE</div>
</section>

<section class="about">
  <svg class="abs" style="left:25px;top:726px" width="260" height="300" viewBox="0 0 260 300"><path d="M0 170 L220 0 L245 20" fill="none" stroke="#333" stroke-width="9"/><path d="M5 170 L95 280" fill="none" stroke="#333" stroke-width="9"/></svg>
  <div class="about-frame"></div>
  <div class="photo about-photo" role="img" aria-label="Clinic building exterior with lawn and blue sky"></div>
  <div class="ghost" style="left:520px;top:788px">ABOUT US</div>
  <div class="about-copy">
    <div class="section-title" style="position:static">ABOUT US</div>
    <h3>Vel Cora is an investment company</h3>
    <p>Vel Cora is an investment company put together by a group of seasoned business professionals who have come together to combine decades of success in the real estate development, management, financing and medical services. The company will be a full service company offering turn key solutions for medical professionals.</p>
    <p style="margin-top:10px">Vel-Cora will focus on providing a full range of services via a group of distinct companies to deliver newly emerging needs of the medical community.</p>
  </div>
  <div class="btn-outline-dark">READ MORE</div>
</section>

<section class="services-band">
  <div class="lead-small center">OUR</div>
  <h2 class="center">SERVICES WE PROVIDE</h2>
  <p>Nemo enim ipsam voluptatem quia voluptas sit aspernatur aut odit aut fugit, sed quia consequuntur magni dolores eos qui ratione voluptatem sequi nesciunt. Neque porro quisquam est.</p>
</section>

<article class="service-card" style="left:110px">
  <div class="photo" role="img" aria-label="Hands working over charts and colour swatches at a desk" style="background:linear-gradient(135deg,#c9c2b8,#8c8f95)"></div>
  <h3 class="blue-text">Management Services</h3>
  <p>Nemo enim ipsam voluptatem quia voluptas sit aspernatur aut odit aut fugit, sed quia consequuntur magni dolores eos qui ratione voluptatem sequi nesciunt.</p>
  <div class="btn-small btn-blue-outline">Read More</div>
</article>
<article class="service-card" style="left:450px">
  <div class="photo" role="img" aria-label="Financial reports and coffee cup on a desk" style="background:linear-gradient(135deg,#6f8fae,#d5dde4)"></div>
  <h3 class="green-text">Financing Services</h3>
  <p>Nemo enim ipsam voluptatem quia voluptas sit aspernatur aut odit aut fugit, sed quia consequuntur magni dolores eos qui ratione voluptatem sequi nesciunt.</p>
  <div class="btn-small btn-green">Read More</div>
</article>
<article class="service-card" style="left:788px">
  <div class="photo" role="img" aria-label="Doctor consulting with a patient in a clinic office" style="background:linear-gradient(135deg,#9aa1a8,#e4e4e2)"></div>
  <h3 class="blue-text" style="top:264px">Medical Services</h3>
  <p>Nemo enim ipsam voluptatem quia voluptas sit aspernatur aut odit aut fugit, sed quia consequuntur magni dolores eos qui ratione voluptatem sequi nesciunt.</p>
  <div class="btn-small btn-blue-outline">Read More</div>
</article>

<section class="partners">
  <div class="ghost center" style="top:2160px">OUR CONSTRUCTION PARTNER</div>
  <div class="section-title center" style="top:2188px">OUR CONSTRUCTION PARTNER</div>
  <div class="partner-box" style="left:238px"><span class="name" style="color:#7a1f2b">NORVIXA</span><span class="sub">Equipment Leasing Inc.</span></div>
  <div class="partner-box" style="left:630px"><span class="name" style="color:#2a3b8f">318 BUILDS INC.</span></div>
</section>

<section class="team-band">
  <div class="ghost center" style="top:56px">OUR MANAGEMENT TEAM</div>
  <div class="section-title center" style="top:87px">OUR MANAGEMENT TEAM</div>
</section>
<article class="team-card" style="left:110px">
  <div class="photo" role="img" aria-label="Portrait of Dr. Gil Parish" style="background:linear-gradient(180deg,#9a9a9a,#6f6f6f)"></div>
  <h3 class="blue-text">Dr. Gil Parish</h3>
  <p>A published author and experienced, board-certified physician in the field of Bioidentical Hormone Replacement Therapy, Dr. Parish believes in a holistic approach to helping men and women look stunning and feel great.</p>
  <div class="btn-small btn-blue">Read More</div>
</article>
<article class="team-card" style="left:620px">
  <div class="photo" role="img" aria-label="Portrait of Dietmar Vellasquin outdoors" style="background:linear-gradient(180deg,#7fa8c9,#4b5b50)"></div>
  <h3 class="green-text">Dietmar Vellasquin</h3>
  <p>Dietmar brings over 25 years of experience in partnering with dentists across Western Canada as a dental consultant. He has been involved in building hundreds of clinics and has assisted clients with clinic location and design.</p>
  <div class="btn-small btn-green">Read More</div>
</article>

<section class="projects">
  <div class="ghost center" style="top:3195px">PROPOSED PROJECTS</div>
  <div class="section-title center" style="top:3223px">PROPOSED PROJECTS</div>
</section>
<article class="project-card" style="left:110px">
  <div class="photo" role="img" aria-label="Glass office towers with palm trees" style="background:linear-gradient(180deg,#8fb6d8,#4f7fa6 60%,#4d7a3e)"></div>
  <div class="label">Pinegrove Business Park</div>
</article>
<article class="project-card featured" style="left:444px">
  <div class="photo" role="img" aria-label="Rendering of a two-storey business park building" style="background:linear-gradient(180deg,#3a3a3a,#8a8a8a 50%,#d8d8d8)"></div>
  <div class="label">Holtmere Business Park</div>
</article>
<article class="project-card" style="left:776px">
  <div class="photo" role="img" aria-label="Interior rendering of a professional building atrium" style="background:linear-gradient(180deg,#a9a9a9,#5e5e5e)"></div>
  <div class="label" style="font-size:16px">Mt. Corwin Ridge Professional</div>
</article>

<footer class="site-footer">
  <div class="footer-brand">VEL-CORA<small>SOLUTIONS</small></div>
  <div class="quick-links">
    <h4>Quick Links</h4>
    <ul style="left:484px;top:120px"><li>&gt;&nbsp;&nbsp;Home</li><li>&gt;&nbsp;&nbsp;About</li><li>&gt;&nbsp;&nbsp;Services</li><li>&gt;&nbsp;&nbsp;Gallery</li><li>&gt;&nbsp;&nbsp;Blog</li></ul>
    <ul style="left:630px;top:120px"><li>&gt;&nbsp;&nbsp;Privacy</li><li>&gt;&nbsp;&nbsp;Contact Us</li></ul>
  </div>
  <div class="footer-contact">
    <div class="contact-row"><span class="contact-icon"><svg width="24" height="24" viewBox="0 0 24 24" fill="none" stroke="#2f2f2f" stroke-width="2"><path d="M12 22s7-7 7-12a7 7 0 0 0-14 0c0 5 7 12 7 12z"/><circle cx="12" cy="10" r="2.5"/></svg></span><div><b>Address:</b><span>PO Box 4471, Larkhaven,<br>TX 70914</span></div></div>
    <div class="contact-row"><span class="contact-icon"><svg width="24" height="24" viewBox="0 0 24 24" fill="none" stroke="#2f2f2f" stroke-width="2"><path d="M5 3h4l2 5-3 2a11 11 0 0 0 6 6l2-3 5 2v4a2 2 0 0 1-2 2A17 17 0 0 1 3 5a2 2 0 0 1 2-2z"/></svg></span><div><b>Phone:</b><span>+1 555 014 2290</span></div></div>
    <div class="contact-row"><span class="contact-icon"><svg width="26" height="20" viewBox="0 0 26 20" fill="none" stroke="#2f2f2f" stroke-width="2"><rect x="1" y="1" width="24" height="18"/><path d="M1 1l12 10L25 1"/></svg></span><div><b>Mail:</b><span>info@velcorahealth.ca</span></div></div>
  </div>
  <div class="footer-rule"></div>
  <div class="copyright">Copyrights @ 2020 Harlow Venn. All Rights Reserved.</div>
  <div class="footer-social"><span></span><span></span><span></span></div>
</footer>

</body>
</html>
```